Brisk Fixwell business card

I need business card for my business, I think you have all my details.six months ago I design with you car wrap design. We would like to design both side of the card. On front of card we would like logo , Name and our contact details.
At the back we are looking to mentioned our services.
The name will be:
Faridoullan Mestor
Managing Director
Ph:07952338417
Email:info@brisk-fixwell.com
Web:www.brisk-fixwell.com
So we have our logo, you don’t need to change the logo.
Please see the attachment.
Thanks

Target Market(s)

Home improvement

Industry/Entity Type

Home Improvement

Contact Information for Business Card

Company name: Brisk Fixwell
Name: Faridoullan Mestor
Position: Director
Ph:07952338417
Web: www.brisk-fixwell.com
Add: 42 Corvale Road
Hounslow
TW3 9KD
SECOND PERSON
Nizamuddel mestor
Position: Handyman
Ph: 07812 564037
Email: info@brisk-fixwell.com
Add: 18 Brackwin Lane Road
Hounslow
TW6 2LB

```html
<!DOCTYPE html>
<html lang="en">
<head>
<meta charset="utf-8">
<title>Brisk Fixwell – Business Card</title>
<link href="https://fonts.googleapis.com/css2?family=Arimo:wght@400;700&display=swap" rel="stylesheet">
<style>
  :root {
    --backdrop: #262626;
    --card: #0c0c0c;
    --brand-blue: #2d3f9c;
    --text-grey: #c9c9c9;
    --silver: #d6d6d6;
    --bullet-red: #e0202f;
    --divider: #2c2c2c;
  }
  * { margin: 0; padding: 0; box-sizing: border-box; }
  html, body {
    width: 1200px; height: 900px; overflow: hidden;
    background: radial-gradient(ellipse at 45% 45%, #333 0%, var(--backdrop) 55%, #161616 100%);
    font-family: "Arimo", Arial, sans-serif;
  }
  .card {
    position: absolute;
    width: 560px; height: 320px;
    background: var(--card);
    border-radius: 22px;
    box-shadow: 0 18px 40px rgba(0,0,0,.6);
    overflow: hidden;
  }
  .card--front { left: 50px; top: 480px; }
  .card--back  { left: 590px; top: 100px; }

  /* front */
  .brand-mark {
    position: absolute; display: flex; align-items: center; gap: 12px;
  }
  .brand-mark__square { width: 18px; height: 18px; }
  .brand-mark__name { font-weight: 700; letter-spacing: .5px; }
  .card--front .brand-mark { left: 52px; top: 176px; }
  .card--front .brand-mark__square { background: var(--brand-blue); }
  .card--front .brand-mark__name { color: var(--brand-blue); font-size: 27px; }

  .divider {
    position: absolute; left: 272px; top: 40px; width: 1px; height: 240px;
    background: var(--divider);
  }
  .contact { position: absolute; left: 300px; top: 66px; color: var(--text-grey); }
  .contact__name {
    color: var(--brand-blue); font-weight: 700; font-size: 18px;
    text-transform: uppercase; letter-spacing: .3px;
  }
  .contact__role { font-size: 13px; text-transform: uppercase; margin-top: 4px; letter-spacing: .5px; }
  .contact__list { list-style: none; margin-top: 16px; font-size: 14px; }
  .contact__list li { display: flex; align-items: center; gap: 10px; height: 22px; }
  .contact__list svg { width: 14px; height: 14px; flex: none; }
  .contact__address { margin-top: 16px; font-size: 14.5px; line-height: 1.45; }

  /* back */
  .card--back .brand-mark { left: 0; right: 0; justify-content: center; top: 92px; }
  .card--back .brand-mark__square { background: var(--silver); }
  .card--back .brand-mark__name { color: var(--silver); font-size: 34px; }

  .services {
    position: absolute; left: 30px; right: 24px; top: 214px;
    display: grid; grid-template-columns: auto auto auto auto auto;
    column-gap: 16px; row-gap: 6px;
    list-style: none; font-size: 13.5px; color: var(--text-grey);
  }
  .services li { display: flex; align-items: center; gap: 5px; white-space: nowrap; }
  .services li::before {
    content: ""; width: 6px; height: 6px; border-radius: 50%; background: var(--bullet-red);
  }
</style>
</head>
<body>

<section class="card card--front" aria-label="Business card front">
  <div class="brand-mark">
    <span class="brand-mark__square"></span>
    <span class="brand-mark__name">Brisk Fixwell</span>
  </div>
  <div class="divider"></div>
  <div class="contact">
    <p class="contact__name">Faridoullan Mestor</p>
    <p class="contact__role">Director</p>
    <ul class="contact__list">
      <li>
        <svg viewBox="0 0 24 24" fill="none" stroke="var(--brand-blue)" stroke-width="2.4" stroke-linecap="round"><path d="M5 3h4l2 5-2.5 1.5a11 11 0 0 0 6 6L16 13l5 2v4a2 2 0 0 1-2 2A17 17 0 0 1 3 5a2 2 0 0 1 2-2z"/></svg>
        07952338417
      </li>
      <li>
        <svg viewBox="0 0 24 24" fill="var(--brand-blue)"><path d="M2 5h20v14H2z"/><path d="M2 5l10 8 10-8" fill="none" stroke="var(--card)" stroke-width="1.6"/></svg>
        info@brisk-fixwell.com
      </li>
      <li>
        <svg viewBox="0 0 24 24" fill="none" stroke="var(--brand-blue)" stroke-width="2"><circle cx="12" cy="12" r="9.5"/><ellipse cx="12" cy="12" rx="4" ry="9.5"/><path d="M2.5 12h19M4.5 7h15M4.5 17h15"/></svg>
        www.brisk-fixwell.com
      </li>
    </ul>
    <p class="contact__address">42 Corvale Road<br>Hounslow, TW3 9KD</p>
  </div>
</section>

<section class="card card--back" aria-label="Business card back">
  <div class="brand-mark">
    <span class="brand-mark__square"></span>
    <span class="brand-mark__name">Brisk Fixwell</span>
  </div>
  <ul class="services">
    <li>Plumbing</li>
    <li>Decking</li>
    <li>Gutter</li>
    <li>Plastering</li>
    <li>Painting &amp; Decorating</li>
    <li>Carpentry</li>
    <li>Fence</li>
    <li>Flooring</li>
    <li>Tilling</li>
    <li>Gardening</li>
  </ul>
</section>

</body>
</html>
```